Business card design for Automotive workshop

We need a business card for a new automotive repair and tyre shop called Keelstone Prime Automotive located in New Zealand. We are a clean, modern and fresh workshop and company.

Front needs to feature logo,
my name:
Marlo Fenwicke (director)

Address:
48 Tarn Lane
Harrowby 3592

Phone: 07 594 2713
Mobile: 027 451 9362
Email: office@keelstoneautomotive.example.nz
Website: keelstoneautomotive.example.nz

Back needs to feature an area to write down appointment details, date and time.

Also feature a list of jobs and work we do such as,
Vehicle Servicing
All Mechanical Repairs
Warrant of Fitness
Tyres & Wheel Alignments
Automotive Diagnostics
Automotive Parts & Supplies

```html
<!DOCTYPE html>
<html lang="en">
<head>
<meta charset="utf-8">
<title>Keelstone Prime Automotive – Business Card</title>
<link href="https://fonts.googleapis.com/css2?family=Lato:wght@400;700;900&family=Roboto:wght@500&display=swap" rel="stylesheet">
<style>
  :root {
    --backdrop: #1d1d1d;
    --card: #ffffff;
    --brand-red: #e3141f;
    --ink: #3a3a3a;
    --ink-soft: #555555;
    --rule: #777777;
  }
  * { box-sizing: border-box; margin: 0; padding: 0; }
  html, body { width: 1200px; height: 900px; overflow: hidden; }
  body {
    background: var(--backdrop);
    font-family: "Lato", sans-serif;
    color: var(--ink);
    position: relative;
  }
  .card {
    position: absolute;
    left: 250px;
    width: 700px;
    height: 400px;
    background: var(--card);
  }
  .card--back { top: 30px; }
  .card--front { top: 470px; }

  .brand-name {
    position: absolute;
    left: 0; right: 0;
    text-align: center;
    font-family: "Lato", sans-serif;
    font-weight: 900;
    font-size: 30px;
    letter-spacing: 3px;
    color: var(--brand-red);
    text-transform: uppercase;
  }
  .card--back .brand-name { top: 48px; }
  .card--front .brand-name { top: 70px; }

  /* Back: appointment */
  .appointment-label {
    position: absolute;
    top: 126px; left: 0; right: 0;
    text-align: center;
    color: var(--brand-red);
    font-size: 16px;
    letter-spacing: 0.5px;
  }
  .appointment-field {
    position: absolute;
    display: flex;
    align-items: flex-end;
    font-size: 16px;
    color: var(--ink-soft);
  }
  .appointment-field .write-line {
    display: inline-block;
    border-bottom: 1px solid var(--rule);
    height: 14px;
    margin-left: 4px;
  }
  .field-date { top: 150px; left: 50px; }
  .field-date .write-line { width: 250px; }
  .field-time { top: 182px; left: 310px; }
  .field-time .write-line { width: 270px; }

  .service-list {
    position: absolute;
    top: 240px; left: 0; right: 0;
    text-align: center;
    list-style: none;
    font-size: 18px;
    line-height: 27px;
    letter-spacing: 0.6px;
    color: var(--ink);
  }
  .service-list .divider { color: var(--brand-red); margin: 0 4px; }

  /* Front: name band */
  .name-band {
    position: absolute;
    top: 196px; left: 0; right: 0;
    height: 1px;
    background: var(--brand-red);
  }
  .person-name {
    position: absolute;
    top: 150px; left: 0; right: 0;
    text-align: center;
    font-family: "Roboto", sans-serif;
    font-weight: 500;
    font-size: 34px;
    color: var(--brand-red);
  }
  .person-role {
    position: absolute;
    top: 196px; left: 50%;
    transform: translate(-50%, -2px);
    background: var(--card);
    padding: 0 6px;
    font-size: 18px;
    color: var(--ink-soft);
    letter-spacing: 0.5px;
  }
  .contact-list {
    position: absolute;
    top: 226px; left: 34px;
    list-style: none;
    font-size: 18px;
    line-height: 26px;
    color: var(--ink-soft);
  }
  .contact-list li { display: flex; align-items: center; gap: 9px; }
  .contact-icon { width: 13px; height: 13px; flex: none; }
  .address {
    position: absolute;
    right: 36px; bottom: 32px;
    text-align: right;
    font-size: 21px;
    line-height: 28px;
    font-style: normal;
    color: var(--ink-soft);
  }
</style>
</head>
<body>

<section class="card card--back" aria-label="Card back">
  <h2 class="brand-name">Keelstone Prime Automotive</h2>
  <p class="appointment-label">Appointment</p>
  <p class="appointment-field field-date">Date<span class="write-line"></span></p>
  <p class="appointment-field field-time">Time<span class="write-line"></span></p>
  <ul class="service-list">
    <li>Vehicle Servicing<span class="divider">|</span>All Mechanical Repairs</li>
    <li>Warrant of Fitness<span class="divider">|</span>Tyres &amp; Wheel Alignments</li>
    <li>Automotive Diagnostics<span class="divider">|</span>Automotive Parts &amp; Supplies</li>
  </ul>
</section>

<section class="card card--front" aria-label="Card front">
  <h1 class="brand-name">Keelstone Prime Automotive</h1>
  <div class="name-band"></div>
  <p class="person-name">Marlo Fenwicke</p>
  <p class="person-role">Director</p>
  <ul class="contact-list">
    <li>
      <svg class="contact-icon" viewBox="0 0 16 16" aria-hidden="true"><path d="M4 1 L6.5 4.5 L5 6.5 Q6.5 9.5 9.5 11 L11.5 9.5 L15 12 L13 15 Q6 14 1 3 Z" fill="#e3141f"/></svg>
      07 594 2713
    </li>
    <li>
      <svg class="contact-icon" viewBox="0 0 16 16" aria-hidden="true"><rect x="4" y="1" width="8" height="14" rx="1.5" fill="none" stroke="#e3141f" stroke-width="1.8"/><circle cx="8" cy="12.3" r="1" fill="#e3141f"/></svg>
      027 451 9362
    </li>
    <li>
      <svg class="contact-icon" viewBox="0 0 16 16" aria-hidden="true"><rect x="1" y="3" width="14" height="10" fill="none" stroke="#e3141f" stroke-width="1.6"/><path d="M1 3 L8 9 L15 3" fill="none" stroke="#e3141f" stroke-width="1.6"/></svg>
      office@keelstoneautomotive.example.nz
    </li>
    <li>
      <svg class="contact-icon" viewBox="0 0 16 16" aria-hidden="true"><g fill="none" stroke="#e3141f" stroke-width="1.4"><circle cx="8" cy="8" r="6.5"/><ellipse cx="8" cy="8" rx="3" ry="6.5"/><path d="M1.5 8 H14.5 M2.5 4.8 H13.5 M2.5 11.2 H13.5"/></g></svg>
      www.keelstoneautomotive.example.nz
    </li>
  </ul>
  <address class="address">48 Tarn Lane<br>Harrowby 3592</address>
</section>

</body>
</html>
```